CREATE A BUSINESS CARD FOR A BOAT CLEANING SERVICE

WE ARE STARTING A NEW BOAT CLEANING BUSINESS. WE DIVE UNDERWATER TO CLEAN BOAT HULLS, JETTIES, UNDERWATER STRUCTURES ETC. WE ARE LOOKING FOR AN UPPERMARKET MODERN LOGO AND BUSINESS CARD AS ALOT OF OUR TARGET MARKET WILL BE HIGH END. YOU HAVE TO DESIGN A BUSINESS CARD AND LOGO SEPERATELY .
THE BUSINESS CARD DIMESNION MUST BE STANDARD SIZE.
The standard dimensions of a printed business card are 3.5 x 2 inches

Target Market(s)

UNDERWATER SERVICED

Industry/Entity Type

Business

Contact Information for Business Card

HOLLAND UNDERWATER SERVICES

Font styles to use
Serif

Colors

Designer to choose colors to be used in the design.

Requirements
Must have
• HOLLAND
Nice to have
• dark
Should not have
• more than 3 colors

```html
<!DOCTYPE html>
<html lang="en">
<head>
<meta charset="utf-8">
<title>Holland Underwater Services – Business Card</title>
<link href="https://fonts.googleapis.com/css2?family=Lato:wght@400;700&display=swap" rel="stylesheet">
<style>
  :root {
    --stage: #d9d6d2;
    --card-top: #2a2c2f;
    --card-bottom: #0d0e10;
    --brand-blue: #2f86d6;
    --badge-blue: #2f7f98;
    --text-light: #f2f2f2;
  }
  html, body {
    margin: 0;
    padding: 0;
    width: 1200px;
    height: 1023px;
    overflow: hidden;
    background: var(--stage);
    font-family: "Lato", sans-serif;
  }
  .canvas {
    position: relative;
    width: 1200px;
    height: 1023px;
    display: flex;
    align-items: center;
    justify-content: center;
  }
  .card {
    position: relative;
    width: 440px;
    height: 770px;
    border-radius: 22px;
    background: linear-gradient(160deg, var(--card-top) 0%, #18191c 55%, var(--card-bottom) 100%);
    box-shadow: 0 18px 40px rgba(0,0,0,0.35);
    color: var(--text-light);
    text-align: center;
    overflow: hidden;
  }
  .company-name {
    position: absolute;
    top: 128px;
    left: 30px;
    right: 30px;
    margin: 0;
    font-size: 30px;
    font-weight: 400;
    line-height: 1.25;
    color: var(--brand-blue);
  }
  .person {
    position: absolute;
    top: 262px;
    left: 0;
    right: 0;
  }
  .person-name {
    margin: 0;
    font-size: 30px;
    font-weight: 400;
    letter-spacing: 4px;
    color: var(--brand-blue);
  }
  .person-role {
    margin: 6px 0 0;
    font-size: 22px;
    color: var(--text-light);
  }
  .contact {
    position: absolute;
    top: 360px;
    left: 0;
    right: 0;
    font-size: 19px;
    line-height: 1.45;
    color: var(--text-light);
  }
  .contact p { margin: 0; }
  .pin {
    display: block;
    margin: 22px auto 10px;
  }
  .footer {
    position: absolute;
    bottom: 52px;
    left: 36px;
    right: 36px;
    display: flex;
    align-items: center;
    justify-content: space-between;
  }
  .partner-badge {
    width: 84px;
    height: 84px;
    border-radius: 50%;
    background: var(--badge-blue);
  }
  .footer-name {
    font-size: 30px;
    font-weight: 400;
    color: var(--text-light);
  }
</style>
</head>
<body>
<main class="canvas">
  <section class="card" aria-label="Holland Underwater Services business card">
    <h1 class="company-name">HOLLAND<br>UNDERWATER SERVICES</h1>

    <div class="person">
      <h2 class="person-name">DAN MEIJER</h2>
      <p class="person-role">CEO / Founder</p>
    </div>

    <div class="contact">
      <p>212-555-0148 | 212-555-0192</p>
      <p>info@hollandunderwaterservice.com</p>
      <p>www.hollandunderwaterservice.com</p>
      <svg class="pin" width="34" height="34" viewBox="0 0 34 34" aria-hidden="true">
        <circle cx="17" cy="17" r="17" fill="#3fa7c4"/>
        <path d="M17 8a6 6 0 0 0-6 6c0 4.5 6 11 6 11s6-6.5 6-11a6 6 0 0 0-6-6z" fill="#fff"/>
        <circle cx="17" cy="14" r="2.2" fill="#3fa7c4"/>
      </svg>
      <p>Havenkade 27 3011AB, Suite<br>-120, Rotterdam, The Netherlands</p>
    </div>

    <footer class="footer">
      <div class="partner-badge" role="img" aria-label="Partner badge"></div>
      <span class="footer-name">HOLLAND</span>
    </footer>
  </section>
</main>
</body>
</html>
```